Wordpress Design for a Digital Management Consulting Business

I need a simple Wordpress Design and someone to set it up for a new boutique management consulting business called Quillon Advisory that specialises in providing strategic advice to help grow digital businesses. It covers business strategy, marketing strategy, digital strategy, web product development, marketing campaigns, social, search, etc. From strategy to implementation.

URL is: quillonadvisory.com.au

My professional background is here: au.linkedin.com/in/hollyprenwick

Competitors: other boutique digital/marketing management consulting businesses in Australia

The logos, colours and fonts are attached.

I would like the site to convey a business that is Smart/intelligent, Contemporary, Progressive, Digital, Energetic, Friendly.

The objective of the site is to educate visitors about what Quillon Advisory does and encourage them to contact me for more information. It will be very light on content.

Target Market(s)

CEOs/Managing Directors, General Managers, Marketing Directors

Industry/Entity Type

Management Consulting

Font styles to use
Sans Serif

Colors
e34197
5c5c5c
000000

Requirements
Must have
• Site design requirements:
• Choose an appropriate Wordpress template, set it up for me and let me be able to edit it ongoing.
• It should use lots of images - these can be inspirational and not necessarily tied directly to the work
• Pink should feature, but not be the dominant colour.
• Site structure should be:
• 1. Home page - image led with horizontal navigation. Text beneath and images to describe the services.
• 2. About page - with space to write text and insert a picture of the Director
• 3. Services - with space to highlight services either as a list or graphically with text
• 4. Contact page - with space to write text and add email links, etc.
• Should have horizontal navigation
• It should have the flexibility to add another page
Nice to have
• Use the tree icon somehow in the design - consider in the background enlarged
• Use pink, grey, black from logo. Can introduce another complimentary colour if necessary.
• Can introduce another complimentary font to go with the logo font.
Should not have
• Use cliched business images and icons, eg. business suits, hand shakes, business men, business ties.

```html
<!DOCTYPE html>
<html lang="en">
<head>
<meta charset="utf-8">
<title>Quillon Advisory</title>
<link href="https://fonts.googleapis.com/css2?family=Open+Sans:wght@300;400;600;700&display=swap" rel="stylesheet">
<style>
:root{
  --pink:#e34197;
  --grey:#5c5c5c;
  --black:#000000;
  --ink:#333333;
  --band:#3b3b3b;
  --light:#efefef;
  --footer:#111111;
  --muted:#9a9a9a;
  --white:#ffffff;
}
*{box-sizing:border-box;margin:0;padding:0}
html,body{width:758px;height:1200px;overflow:hidden;background:var(--white)}
body{font-family:'Open Sans',Arial,sans-serif;color:var(--ink);position:relative}
.page{position:relative;width:758px;height:1200px;overflow:hidden}

/* header */
.site-header{position:absolute;top:0;left:0;width:758px;height:68px;background:var(--white)}
.brand{position:absolute;left:60px;top:16px;display:flex;align-items:center;gap:10px}
.brand-mark{width:30px;height:30px;border-radius:50%;background:var(--pink)}
.brand-name{font-size:17px;font-weight:600;color:var(--pink);letter-spacing:1px;text-transform:uppercase;line-height:1.05;width:110px}
.main-nav{position:absolute;right:60px;top:30px;display:flex;gap:30px}
.main-nav a{font-size:9.5px;color:var(--grey);text-decoration:none;text-transform:uppercase;letter-spacing:.5px}
.main-nav a.active{color:var(--pink)}

/* hero */
.hero{position:absolute;top:68px;left:0;width:758px;height:255px;
  background:linear-gradient(120deg,#f3e4ea 0%,#dbc8cf 35%,#b88f9c 60%,#8a6a74 80%,#cbb9be 100%)}
.hero-panel{position:absolute;left:58px;top:58px;width:285px;padding:16px 18px;background:rgba(255,255,255,.82)}
.hero-panel h1{font-size:23px;font-weight:400;color:var(--black);margin-bottom:8px}
.hero-panel p{font-size:10px;line-height:1.45;color:var(--grey)}

/* intro band */
.intro-band{position:absolute;top:323px;left:0;width:758px;height:81px;background:var(--band);padding:16px 63px}
.intro-band p{font-size:9px;line-height:1.55;color:#e6e6e6}
.intro-band strong{color:var(--white);font-weight:700}

/* section headings */
.section-title{position:absolute;left:63px;font-size:25px;font-weight:300;color:var(--black)}
.section-rule{position:absolute;left:170px;right:63px;height:1px;background:#d6d6d6}

/* services */
.service{position:absolute;top:462px;width:197px}
.service .photo{width:197px;height:94px}
.service h3{font-size:14px;font-weight:400;color:var(--pink);margin:18px 0 6px}
.service p{font-size:8.5px;line-height:1.45;color:var(--grey)}
.service .more{display:block;font-size:9px;font-weight:600;color:var(--ink);margin-top:10px;text-decoration:none}

/* what we do */
.what-we-do{position:absolute;top:700px;left:0;width:758px;height:300px;background:var(--light)}
.approach{position:absolute;top:58px;width:197px}
.approach .photo{width:197px;height:96px;border:4px solid var(--white);box-shadow:0 1px 3px rgba(0,0,0,.15)}
.approach h3{font-size:14px;font-weight:400;color:var(--ink);margin:14px 0 6px;line-height:1.2;min-height:34px}
.approach p{font-size:8.5px;line-height:1.45;color:var(--grey)}
.btn{display:inline-block;margin-top:10px;padding:4px 9px;border:1px solid #c9c9c9;background:var(--white);font-size:9px;color:var(--ink);text-decoration:none}

/* footer */
.site-footer{position:absolute;top:1000px;left:0;width:758px;height:168px;background:var(--footer);color:var(--muted)}
.footer-col{position:absolute;top:22px}
.footer-col h4{font-size:19px;font-weight:300;color:var(--white);margin-bottom:12px}
.footer-col ul{list-style:none}
.footer-col li{font-size:8.5px;line-height:1.75;padding-left:10px;position:relative}
.footer-col li::before{content:"›";position:absolute;left:0;color:var(--pink)}
.service-lists{display:flex;gap:60px}
.contact-line{display:flex;align-items:center;gap:8px;font-size:8.5px;margin-bottom:8px}
.contact-line svg{flex:none}
.social{display:flex;gap:8px;margin-top:6px}
.social span{width:17px;height:17px;border-radius:50%;border:1px solid var(--muted)}
.copyright{position:absolute;top:1168px;left:0;width:758px;height:32px;background:var(--pink);color:var(--white);font-size:8.5px;text-align:center;line-height:32px}
</style>
</head>
<body>
<div class="page">

  <header class="site-header">
    <div class="brand">
      <span class="brand-mark"></span>
      <span class="brand-name">Quillon Advisory</span>
    </div>
    <nav class="main-nav">
      <a class="active" href="#">Home</a>
      <a href="#">Services</a>
      <a href="#">About</a>
      <a href="#">Clients</a>
      <a href="#">Contact us</a>
    </nav>
  </header>

  <section class="hero" role="img" aria-label="Photo of a hand touching a tablet screen">
    <div class="hero-panel">
      <h1>Quillon Advisory</h1>
      <p>Boutique management consulting company assisting digital businesses across business product and marketing strategy.</p>
    </div>
  </section>

  <section class="intro-band">
    <p><strong>QUILLON ADVISORY</strong> was founded in July 2014 and has provided strategic advice to a range of large corporate clients and small entrepreneurial businesses around Australia and internationally. The face of Quillon Advisory is Holly Prenwick who's 15 years digital and strategic experience working thinly drawn on experts as projects require.</p>
  </section>

  <h2 class="section-title" style="top:418px">Our Services</h2>
  <div class="section-rule" style="top:436px;left:220px"></div>

  <article class="service" style="left:63px">
    <div class="photo" role="img" aria-label="Photo of a team working at laptops" style="background:linear-gradient(135deg,#c7d3dd,#8ea3b3 60%,#dfe5ea)"></div>
    <h3>Digital Strategy</h3>
    <p>Lorem ipsum dolor sit amet, consectetur adipisici elit, sed eiusmod tempor incidunt ut labore et dolore magna aliqua.</p>
    <a class="more" href="#">Read more.</a>
  </article>
  <article class="service" style="left:281px">
    <div class="photo" role="img" aria-label="Photo of a person writing at a desk" style="background:linear-gradient(135deg,#f2f2f2,#c9c9c9 55%,#8a8a8a)"></div>
    <h3>Marketing Strategy</h3>
    <p>Lorem ipsum dolor sit amet, consectetur adipisici elit, sed eiusmod tempor incidunt ut labore et dolore magna aliqua.</p>
    <a class="more" href="#">Read more.</a>
  </article>
  <article class="service" style="left:499px">
    <div class="photo" role="img" aria-label="Illustration of connected digital devices" style="background:linear-gradient(135deg,#1c3550,#3f6c93 55%,#9bb8cf)"></div>
    <h3>Digital Transformation</h3>
    <p>Lorem ipsum dolor sit amet, consectetur adipisici elit, sed eiusmod tempor incidunt ut labore et dolore magna aliqua.</p>
    <a class="more" href="#">Read more.</a>
  </article>

  <section class="what-we-do">
    <h2 class="section-title" style="top:14px">What we do</h2>
    <div class="section-rule" style="top:34px;left:205px"></div>

    <article class="approach" style="left:63px">
      <div class="photo" role="img" aria-label="Photo of a strategy meeting" style="background:linear-gradient(135deg,#e9dccf,#b99a82 55%,#6f5a4d)"></div>
      <h3>Strategic Thinking</h3>
      <p>Lorem Ipsum has been the industry's standard ipsum dolor sit amet, consectetur adipisici elit, sed eiusmod tempor.</p>
      <a class="btn" href="#">Read more.</a>
    </article>
    <article class="approach" style="left:281px">
      <div class="photo" role="img" aria-label="Photo of charts on paper" style="background:linear-gradient(135deg,#f4f4f4,#d2d2d2 60%,#a9a9a9)"></div>
      <h3>Analytical Approach</h3>
      <p>Lorem Ipsum has been the industry's standard ipsum dolor sit amet, consectetur adipisici elit, sed eiusmod tempor.</p>
      <a class="btn" href="#">Read more.</a>
    </article>
    <article class="approach" style="left:499px">
      <div class="photo" role="img" aria-label="Photo of a project team at a table" style="background:linear-gradient(135deg,#d9e1e8,#9fb0bf 55%,#5d6b78)"></div>
      <h3>End to end project Management</h3>
      <p>Lorem Ipsum has been the industry's standard ipsum dolor sit amet.</p>
      <a class="btn" href="#">Read more.</a>
    </article>
  </section>

  <footer class="site-footer">
    <div class="footer-col" style="left:63px">
      <h4>Links</h4>
      <ul><li>Home</li><li>Our Services</li><li>About Us</li><li>Clients</li><li>Contact Us</li></ul>
    </div>
    <div class="footer-col" style="left:190px">
      <h4>Services</h4>
      <div class="service-lists">
        <ul><li>Business Strategy</li><li>Digital Strategy</li><li>Marketing Strategy</li><li>Product Strategy</li><li>Marketing Campaigns</li></ul>
        <ul><li>Product Management</li><li>Digital Marketing</li><li>Search Strategy</li><li>Content Marketing</li><li>New Product Launches</li></ul>
      </div>
    </div>
    <div class="footer-col" style="left:513px">
      <h4>Contact Us</h4>
      <div class="contact-line">
        <svg width="11" height="11" viewBox="0 0 24 24"><path fill="#9a9a9a" d="M6.6 10.8a15.1 15.1 0 0 0 6.6 6.6l2.2-2.2a1 1 0 0 1 1-.25 11.4 11.4 0 0 0 3.6.57 1 1 0 0 1 1 1V20a1 1 0 0 1-1 1A17 17 0 0 1 3 4a1 1 0 0 1 1-1h3.5a1 1 0 0 1 1 1c0 1.25.2 2.45.57 3.57a1 1 0 0 1-.25 1z"/></svg>
        <span>Holly Prenwick &nbsp;0491 570 156</span>
      </div>
      <div class="contact-line">
        <svg width="11" height="11" viewBox="0 0 24 24"><rect x="2" y="5" width="20" height="14" rx="1" fill="none" stroke="#9a9a9a" stroke-width="2"/><path d="M2 6l10 7 10-7" fill="none" stroke="#9a9a9a" stroke-width="2"/></svg>
        <span>holly@quillonadvisory.com.au</span>
      </div>
      <div class="social"><span></span><span></span><span></span><span></span></div>
    </div>
  </footer>
  <div class="copyright">© 2015 Copyright Quillon Advisory. All Right Reserved</div>

</div>
</body>
</html>
```